Satchel & Sundial needs new business card design

I need a new business card design. I'm looking for out-of-the-box design which represents the freedom of being a location independent entrepreneur.
I offer coaching, retreats and trips.
I would like to see designs with and without the photo.
Colors I use are black (#000000), green (#25A796) and brown (#D7C38C)
Website satchelandsundial.example

Target Market(s)

location independent entrepreneurs, digital nomads, people looking to swap the 9 to 5 for a lifestyle business

Industry/Entity Type

Business

Contact Information for Business Card

Dorota Falkner
Your Lifestyle Business Coach, Retreat & Trip Leader
http://satchelandsundial.example
hello@satchelandsundial.example
Live a life you don't need a holiday from

Font styles to use
Serif
Sans Serif

Requirements
Must have
• One side should contain only the logo. I would also consider having the "Live a life you don't need a holiday from" on that side too (depending on how it looks)
• Please show both sides on the designs.

```html
<!DOCTYPE html>
<html lang="en">
<head>
<meta charset="utf-8">
<title>Satchel &amp; Sundial — Business Card</title>
<link rel="stylesheet" href="https://fonts.googleapis.com/css2?family=Lato:wght@400;700;900&family=Special+Elite&display=swap">
<style>
  :root {
    --backdrop: #000000;
    --card-light: #f3f3f3;
    --brand-green: #25a796;
    --ink: #1a1a1a;
    --paper-white: #ffffff;
  }
  html, body {
    margin: 0;
    padding: 0;
    width: 1200px;
    height: 900px;
    overflow: hidden;
    background: var(--backdrop);
  }
  .stage {
    position: relative;
    width: 1200px;
    height: 900px;
    background: var(--backdrop);
    font-family: "Lato", Arial, sans-serif;
  }
  .card {
    position: absolute;
    top: 200px;
    width: 310px;
    height: 502px;
    box-sizing: border-box;
    overflow: hidden;
  }
  .card--front {
    left: 265px;
    background: var(--card-light);
    border-radius: 56px 0 56px 0;
    color: var(--ink);
  }
  .card--back {
    left: 641px;
    width: 309px;
    background: var(--brand-green);
    border-radius: 0 56px 0 56px;
    color: var(--paper-white);
  }
  .wordmark {
    position: absolute;
    font-family: "Lato", Arial, sans-serif;
    font-weight: 900;
    font-size: 23px;
    line-height: 30px;
    text-transform: uppercase;
    letter-spacing: 0.6px;
    white-space: nowrap;
    margin: 0;
  }
  .card--front .wordmark {
    left: 34px;
    top: 112px;
    color: var(--ink);
  }
  .card--back .wordmark {
    left: 0;
    right: 0;
    top: 152px;
    text-align: center;
    color: var(--paper-white);
  }
  .contact-name {
    position: absolute;
    left: 34px;
    top: 266px;
    margin: 0;
    font-size: 19px;
    font-weight: 700;
    letter-spacing: 0.3px;
    color: var(--brand-green);
    text-transform: uppercase;
    white-space: nowrap;
  }
  .contact-role {
    position: absolute;
    left: 34px;
    top: 289px;
    margin: 0;
    font-size: 13.5px;
    line-height: 20px;
    color: var(--ink);
  }
  .contact-list {
    position: absolute;
    left: 34px;
    top: 352px;
    margin: 0;
    padding: 0;
    list-style: none;
    font-size: 13.5px;
    line-height: 19px;
    color: var(--ink);
    white-space: nowrap;
  }
  .contact-list li {
    display: flex;
    align-items: center;
    gap: 6px;
  }
  .contact-list svg {
    width: 9px;
    height: 9px;
    flex: none;
  }
  .tagline {
    position: absolute;
    left: 34px;
    top: 416px;
    margin: 0;
    font-family: "Special Elite", "Courier New", monospace;
    font-size: 13px;
    line-height: 20px;
    letter-spacing: 0.6px;
    text-transform: uppercase;
    color: var(--ink);
    white-space: nowrap;
  }
  .services {
    position: absolute;
    left: 0;
    right: 0;
    top: 404px;
    margin: 0;
    text-align: center;
    font-size: 15.5px;
    letter-spacing: 1.1px;
    text-transform: uppercase;
    color: var(--paper-white);
    white-space: nowrap;
  }
</style>
</head>
<body>
  <main class="stage">
    <section class="card card--front" aria-label="Card front">
      <h1 class="wordmark">Satchel &amp; Sundial</h1>
      <h2 class="contact-name">Dorota Falkner</h2>
      <p class="contact-role">Your Lifestyle Business Coach,<br>Retreat &amp; Trip Leader</p>
      <ul class="contact-list">
        <li>
          <svg viewBox="0 0 10 10" aria-hidden="true">
            <rect x="0.5" y="1.5" width="9" height="7" fill="var(--brand-green)"/>
            <polyline points="0.5,1.5 5,5.5 9.5,1.5" fill="none" stroke="var(--card-light)" stroke-width="1"/>
          </svg>
          hello@satchelandsundial.example
        </li>
        <li>
          <svg viewBox="0 0 10 10" aria-hidden="true">
            <circle cx="5" cy="5" r="4.6" fill="var(--brand-green)"/>
            <path d="M3 3 Q5 4 4 6 Q6 6 7 8" fill="none" stroke="var(--card-light)" stroke-width="0.9"/>
          </svg>
          www.satchelandsundial.example
        </li>
      </ul>
      <p class="tagline">Live a life you don't need<br>a holiday from</p>
    </section>

    <section class="card card--back" aria-label="Card back">
      <h2 class="wordmark">Satchel &amp; Sundial</h2>
      <p class="services">Coaching | Retreats | Trips</p>
    </section>
  </main>
</body>
</html>
```